Web Design Project

Please take a look at my current aged website www.talvikhrconsulting.com and my newly designed logo and business cards. I would like a new fresh updated look to my website and my new designs incorporated.
Updates

  Good Morning Everyone

Due to an Austrralian licencing issue I have had to have my logo slightly redesigned.

Would you please be able to look at the newly uploaded files and revise your designs.

Thanks so much.  I am very happy with the calibre and quality of the designs so far.

kind Regards

Marla

Industry/Entity Type

Business

Requirements
Must have
• the exisiting pages and fresh new graphics and a real commitment to my palette of lime green, turqouise and black.

```html
<!DOCTYPE html>
<html lang="en">
<head>
<meta charset="utf-8">
<title>Talvik Consulting – Human Resources and Recruitment Solutions</title>
<link href="https://fonts.googleapis.com/css2?family=Source+Sans+3:wght@400;600&display=swap" rel="stylesheet">
<style>
:root{
  --teal:#0f8fa8;
  --teal-head:#1487a3;
  --turquoise:#17a9c9;
  --lime:#8cc63f;
  --text:#555;
  --rule:#dcdcdc;
  --orange:#f07a12;
  --orange-light:#f7a43a;
  --white:#fff;
}
*{margin:0;padding:0;box-sizing:border-box}
html,body{width:1200px;height:1161px;overflow:hidden;background:var(--white)}
body{position:relative;font-family:"Source Sans 3",Arial,sans-serif;color:var(--text)}
.abs{position:absolute}
.top-band{left:0;top:0;width:1200px;height:6px;background:var(--turquoise)}
.header{left:0;top:6px;width:1200px;height:117px;background:linear-gradient(#e9f5d6 0,#fff 45px)}
.brand{left:185px;top:48px;display:flex;align-items:center;gap:10px}
.brand-mark{width:52px;height:52px;border-radius:50%;background:var(--lime)}
.brand-name{font-size:25px;font-weight:600;color:var(--teal);line-height:1}
.brand-tag{font-size:7.5px;color:#333;margin-top:2px;letter-spacing:.2px}
.main-nav{left:438px;top:57px;width:582px;height:31px;border-radius:14px;background:linear-gradient(#3bbcd8,#1591ad);box-shadow:0 5px 4px -2px rgba(0,0,0,.45);display:flex}
.main-nav a{flex:1;color:var(--white);font-size:12.5px;text-decoration:none;text-align:center;line-height:31px;border-left:1px solid #0e7791}
.main-nav a:first-child{border-left:none}
.hero{left:0;top:123px;width:1200px;height:320px;background:linear-gradient(#e8e8e8,#fff 60%);border-bottom:1px solid #ddd}
.hero-title{left:210px;top:185px;font-size:27px;line-height:32px;color:var(--teal-head);font-weight:400}
.hero-text{left:213px;top:265px;width:362px;font-size:12px;line-height:19px;text-align:justify}
.slider-dots{left:217px;top:389px;display:flex;gap:6px}
.slider-dots span{width:13px;height:13px;border-radius:50%;background:#c4c4c4}
.slider-dots span.active{background:var(--turquoise)}
.hero-visual{left:630px;top:144px;width:381px;height:299px;background:linear-gradient(#eef3f8,#6b9fd6 55%,#dfeaf4)}
.section-title{font-size:19px;font-weight:400;color:var(--teal-head)}
.rule{height:1px;background:var(--rule)}
.welcome-text{left:171px;top:526px;width:583px;font-size:12px;line-height:20.5px;text-align:justify}
.welcome-photo{left:781px;top:528px;width:255px;height:120px;border:1px solid #aaa;background:linear-gradient(120deg,#3c3f45,#a6a9ae 55%,#e8e8e8)}
.col-text{font-size:12px;line-height:20.3px}
.col-text.justify{text-align:justify}
.col-visual{height:150px}
.read-more{width:98px;height:26px;border-radius:13px;background:linear-gradient(var(--orange-light),var(--orange));color:var(--white);font-size:12px;line-height:26px;padding-left:15px;text-decoration:none}
.footer{left:0;top:1064px;width:1200px;height:97px;background:linear-gradient(#0fb0d4,#0d98b9)}
.footer-nav{left:174px;top:1091px;font-size:12px;color:var(--white)}
.footer-nav a{color:var(--white);text-decoration:none}
.footer-nav .sep{margin:0 8px}
.copyright{left:174px;top:1115px;font-size:12px;color:var(--white)}
.follow{left:843px;top:1103px;font-size:14px;color:var(--white)}
.social{left:921px;top:1093px;display:flex;gap:6px}
.social span{width:31px;height:31px;border-radius:50%;background:#f4f6f7;box-shadow:0 1px 2px rgba(0,0,0,.3)}
</style>
</head>
<body>
<div class="abs top-band"></div>
<header class="abs header"></header>
<div class="abs brand">
  <span class="brand-mark"></span>
  <div>
    <div class="brand-name">Talvik Consulting</div>
    <div class="brand-tag">Human Resources and Recruitment Solutions</div>
  </div>
</div>
<nav class="abs main-nav">
  <a href="#">Home</a><a href="#">Our Services</a><a href="#">Our Consultants</a><a href="#">Our Fees</a><a href="#">Contact Us</a>
</nav>

<section class="abs hero"></section>
<h1 class="abs hero-title">Outsourced Human Resources<br>Solutions and Strategies</h1>
<p class="abs hero-text">During these challenging economic times it can be difficult to justify internal human resources management services or support. However as a business owner or Manager you may find that HR support or advice is required from time to time.</p>
<div class="abs slider-dots"><span class="active"></span><span></span><span></span><span></span><span></span></div>
<div class="abs hero-visual" role="img" aria-label="Illustration of a red figure on a podium surrounded by a circle of blue figures"></div>

<h2 class="abs section-title" style="left:169px;top:475px">Welcome to Our Site</h2>
<div class="abs rule" style="left:165px;top:507px;width:870px"></div>
<p class="abs welcome-text">During these challenging economic times it can be difficult to justify internal human resources management services or support. However as a business owner or Manager you may find that HR support or advice is required from time to time.&nbsp; Talvik HR Consulting are an outsourced HR function.&nbsp; We can provide you with that ongoing support, offer solutions and assist you with developing strategies that fit your business and deliver results. By outsourcing some or all of your HR function you will effectively manage your costs, be able to focus on your core business and still have access to professional up-to-date HR advice, systems and processes.</p>
<div class="abs welcome-photo" role="img" aria-label="Photo of three business people reviewing work together"></div>
<div class="abs rule" style="left:165px;top:688px;width:870px"></div>

<h2 class="abs section-title" style="left:169px;top:709px">Our Services</h2>
<div class="abs rule" style="left:165px;top:742px;width:239px"></div>
<div class="abs col-visual" style="left:193px;top:758px;width:192px;background:radial-gradient(ellipse at 40% 65%,#4aa6dc,#bfe0f2 60%,#fff 80%)" role="img" aria-label="Illustration of blue figures beside a podium with a rising chart"></div>
<p class="abs col-text" style="left:174px;top:922px;width:230px">Attraction, Recruitment and Induction<br>Remuneration, Benefits and Salary<br>Talent Management and Retention<br>Graduate Management</p>
<a class="abs read-more" href="#" style="left:174px;top:1011px">Read More +</a>

<h2 class="abs section-title" style="left:474px;top:709px">Our Consultants</h2>
<div class="abs rule" style="left:471px;top:742px;width:239px"></div>
<div class="abs col-visual" style="left:463px;top:742px;width:245px;height:183px;background:radial-gradient(circle at 50% 50%,#fff 22%,#e0d64a 30%,#5fa24a 45%,#fff 62%)" role="img" aria-label="Illustration of four coloured figures holding hands in a circle"></div>
<p class="abs col-text justify" style="left:474px;top:922px;width:263px">With over ten years human resources experience in the mining, allied health, hospitality, manufacturing, asset management and labour hire industries our Principal Consultant Marla</p>
<a class="abs read-more" href="#" style="left:478px;top:1011px">Read More +</a>

<h2 class="abs section-title" style="left:803px;top:709px">Our Fees</h2>
<div class="abs rule" style="left:799px;top:742px;width:240px"></div>
<div class="abs col-visual" style="left:845px;top:758px;width:140px;background:radial-gradient(ellipse at 55% 50%,#8a8d90,#d6d7d8 55%,#fff 78%)" role="img" aria-label="Illustration of a figure leaning on a large calculator"></div>
<p class="abs col-text justify" style="left:800px;top:922px;width:263px">Our highly competitive fees will be tailored to suit your organisation’s individual needs.&nbsp; Generally the Consultant’s time will be charged at an hourly rate however some projects...</p>
<a class="abs read-more" href="#" style="left:804px;top:1011px">Read More +</a>

<footer class="abs footer"></footer>
<nav class="abs footer-nav">
  <a href="#">Home</a><span class="sep">|</span><a href="#">Our Services</a><span class="sep">|</span><a href="#">Our Consultants</a><span class="sep">|</span><a href="#">Our Fees</a><span class="sep">|</span><a href="#">Contact Us</a>
</nav>
<p class="abs copyright">Copyrights @ 2012 All Rights Reserved</p>
<p class="abs follow">Follow Us</p>
<div class="abs social" aria-label="Social links"><span></span><span></span><span></span><span></span></div>
</body>
</html>
```